Brochure for a paper wholesaler who wants to educate his print industry clients

We will be making a stapled informative brochure, that contains basic information about our paper products - the types of paper there is, their characteristics and other useful information.
As we are part of a paper wholesaler group in Europe - ORVALT, we received a brochure in German that has this kind of information. The text in it is not as important. What is important is the layout of the document and how the text will appear in it (added in the uploaded files - 210915_Wiessenswertes_TBKU_H73.pdf).
We are allowed to tinker with this file and adjust it to our needs. So there are also .idml and .indd files available (also in the uploaded files).
We would like to keep the custom page size of 210 x290mm (8.3x11.4 in), or you can go up to 210x297mm (8.3x11.7 in).
What we want is a modern looking design that contains our companies red bordo and white/ grey colours to replace the existing green colours in this borchure. The pictures and appearance of the file can be changed according to your views and what you think would look good. We don't necessarily want to keep the same design, we just want the layout of the document be the same, as we will be placing our translated text into it. The ORVALT logo should be replaced with our own logo (KENDRO Logo.png).
As for how it could look, it could go together with our paper presentation, for which the design can be seen in the "KENDRO Base - v2.pptx".
Holiday season, so have a lot of tasks to take care of and not as much time to check MakerHive as often.

```html
<!DOCTYPE html>
<html lang="de">
<head>
<meta charset="utf-8">
<title>Wissenswert! – Brochure Cover</title>
<link rel="stylesheet" href="https://fonts.googleapis.com/css2?family=Josefin+Sans:ital,wght@0,300;0,400;0,600;1,600&display=swap">
<style>
  :root {
    --bordo: #7d2a30;
    --bordo-deep: #6a2026;
    --paper: #ffffff;
    --paper-shade: #e6e5ea;
    --ink-grey: #6f6f73;
    --stage: #d9d9db;
  }
  * { margin: 0; padding: 0; box-sizing: border-box; }
  html, body {
    width: 1200px;
    height: 900px;
    overflow: hidden;
    background: var(--stage);
    font-family: "Josefin Sans", sans-serif;
  }
  .cover {
    position: absolute;
    left: 296px;
    top: 30px;
    width: 608px;
    height: 840px;
    background: var(--paper);
    overflow: hidden;
  }
  .cover-visual {
    position: absolute;
    left: 0; top: 0;
    width: 100%;
    height: 420px;
    background:
      radial-gradient(ellipse 70% 60% at 30% 30%, #f3f2f6 0%, rgba(243,242,246,0) 70%),
      linear-gradient(180deg, var(--paper-shade) 0%, #efeef2 55%, var(--paper) 100%);
  }
  .badge {
    position: absolute;
    left: 448px;
    top: 166px;
    width: 124px;
    height: 124px;
    border-radius: 50%;
    background: var(--paper);
    box-shadow: 0 4px 14px rgba(0,0,0,0.10);
    display: flex;
    align-items: center;
    justify-content: center;
    text-align: center;
    color: var(--bordo);
    font-weight: 300;
    font-size: 10.5px;
    line-height: 1.9;
    letter-spacing: 0.06em;
    text-transform: uppercase;
  }
  .title-block {
    position: absolute;
    left: 0;
    top: 486px;
    width: 100%;
    text-align: center;
  }
  .kicker {
    color: var(--ink-grey);
    font-weight: 300;
    font-size: 11.5px;
    letter-spacing: 0.08em;
    text-transform: uppercase;
    margin-bottom: 14px;
  }
  .headline {
    color: var(--bordo);
    font-weight: 400;
    font-size: 30px;
    line-height: 1.08;
    letter-spacing: 0.02em;
    text-transform: uppercase;
  }
  .subline {
    margin-top: 8px;
    color: var(--ink-grey);
    font-style: italic;
    font-weight: 600;
    font-size: 13px;
    letter-spacing: 0.04em;
  }
  .brand {
    position: absolute;
    left: 0;
    top: 680px;
    width: 100%;
    display: flex;
    flex-direction: column;
    align-items: center;
    gap: 12px;
    color: var(--bordo);
  }
  .brand-square {
    width: 34px;
    height: 34px;
    border: 1.5px solid var(--bordo);
  }
  .brand-name {
    font-weight: 300;
    font-size: 15px;
    letter-spacing: 0.55em;
    padding-left: 0.55em;
  }
  .edge-band {
    position: absolute;
    left: 0;
    bottom: 0;
    width: 100%;
    height: 7px;
    background: var(--bordo-deep);
  }
</style>
</head>
<body>
  <main class="cover">
    <div class="cover-visual" role="img" aria-label="Photograph of curled white paper sheets fanning across the top of the cover"></div>

    <div class="badge">Die kleine<br>Papier- und<br>Farbfibel</div>

    <section class="title-block">
      <p class="kicker">Paper &amp; Print</p>
      <h1 class="headline">Wissenswert!<br>Formate, Klassen,<br>Farben, Berechnungen</h1>
      <p class="subline">Wegweiser für den Umgang mit Papier und Karton</p>
    </section>

    <div class="brand">
      <span class="brand-square"></span>
      <span class="brand-name">KENDRO</span>
    </div>

    <div class="edge-band"></div>
  </main>
</body>
</html>
```